Business card design

We need a business card designed completed for a new company. We are a company that works with associations, schools to convert their older text/DVDs into dynamic online and mobile programs. Our initial platform is designed for the legal associations and will enable their lawyers to access their content such as forms, videos, case law and support materials anywhere, anytime. We are also focused on Project Management Associations, Financial Management Associations and IT Associations.

I would like for the business card to have the following information:

Logo

Kent marrowby

President and CEO

kmarrowby@trevantiq.example

Mobile: 555-374-9160

www.trevantiq.example

Tag line: Transforming content into a mobile platform    

I would like it to be double sided, use the colours of the logo, tie into the mobile world

 

Industry/Entity Type

Legal

Logo Text

Trevantiq

```html
<!DOCTYPE html>
<html lang="en">
<head>
<meta charset="utf-8">
<title>Trevantiq business card</title>
<link rel="stylesheet" href="https://fonts.googleapis.com/css2?family=Open+Sans:wght@400;600;700&display=swap">
<style>
  :root {
    --stage: #8a6246;
    --label: #1c1c1c;
    --card-grey: #9a9a9a;
    --card-white: #ffffff;
    --band: #6a6a6a;
    --ink-dark: #2a2a2a;
    --ink-mid: #555555;
    --ink-light: #ffffff;
    --rule-light: #ffffff;
    --rule-grey: #9a9a9a;
  }
  * { margin: 0; padding: 0; box-sizing: border-box; }
  html, body { width: 1200px; height: 800px; overflow: hidden; }
  body {
    position: relative;
    background: var(--stage);
    font-family: "Open Sans", sans-serif;
  }
  .view-label {
    position: absolute;
    width: 200px;
    text-align: center;
    font-size: 20px;
    color: var(--label);
  }
  .card {
    position: absolute;
    width: 510px;
    height: 290px;
    border-radius: 22px;
    overflow: hidden;
  }
  .card--grey { background: var(--card-grey); }
  .card--white { background: var(--card-white); }

  .wordmark {
    position: absolute;
    left: 0; right: 0;
    text-align: center;
    font-weight: 700;
    letter-spacing: -1px;
    line-height: 1;
  }
  .card--grey .wordmark { color: var(--ink-light); }
  .card--white .wordmark { color: var(--ink-mid); }
  .wordmark--small { top: 48px; font-size: 62px; }
  .wordmark--large { top: 102px; font-size: 80px; }

  .identity {
    position: absolute;
    right: 268px;
    top: 174px;
    text-align: right;
    color: var(--ink-dark);
  }
  .identity__name { font-size: 16px; line-height: 20px; }
  .identity__title { font-size: 12px; line-height: 18px; }

  .divider {
    position: absolute;
    left: 255px;
    top: 161px;
    width: 1px;
    height: 61px;
    background: var(--ink-dark);
  }
  .contact {
    position: absolute;
    left: 266px;
    top: 158px;
    list-style: none;
    font-size: 13.5px;
    line-height: 23px;
    color: var(--ink-dark);
  }
  .contact__key { font-weight: 700; font-style: italic; }

  .rule {
    position: absolute;
    left: 0; right: 0;
    top: 248px;
    height: 4px;
  }
  .card--grey .rule { background: var(--rule-light); }
  .card--white .rule { background: var(--rule-grey); height: 3px; top: 249px; }
  .tagline-band {
    position: absolute;
    left: 0; right: 0;
    top: 254px;
    bottom: 0;
    background: var(--band);
    color: var(--ink-light);
    font-size: 15px;
    text-align: center;
    line-height: 36px;
  }
  .web {
    position: absolute;
    left: 0; right: 0;
    top: 252px;
    text-align: center;
    font-size: 16px;
    letter-spacing: 3px;
    color: var(--ink-dark);
  }
</style>
</head>
<body>
  <p class="view-label" style="left:229px; top:50px;">Front</p>
  <section class="card card--grey" style="left:80px; top:97px;">
    <p class="wordmark wordmark--small">Trevantiq</p>
    <div class="identity">
      <p class="identity__name">Kent marrowby</p>
      <p class="identity__title">President and CEO</p>
    </div>
    <span class="divider"></span>
    <ul class="contact">
      <li><span class="contact__key">c</span> : 555-374-9160</li>
      <li>e : kmarrowby@trevantiq.example</li>
      <li>w : www.trevantiq.example</li>
    </ul>
    <span class="rule"></span>
    <p class="tagline-band">Transforming content into a mobile platform</p>
  </section>

  <p class="view-label" style="left:787px; top:50px;">Back - 1</p>
  <section class="card card--white" style="left:638px; top:97px;">
    <p class="wordmark wordmark--small">Trevantiq</p>
    <div class="identity">
      <p class="identity__name">Kent marrowby</p>
      <p class="identity__title">President and CEO</p>
    </div>
    <span class="divider"></span>
    <ul class="contact">
      <li><span class="contact__key">c</span> : 555-374-9160</li>
      <li>e : kmarrowby@trevantiq.example</li>
      <li>w : www.trevantiq.example</li>
    </ul>
    <span class="rule"></span>
    <p class="tagline-band">Transforming content into a mobile platform</p>
  </section>

  <p class="view-label" style="left:231px; top:410px;">Back - 2</p>
  <section class="card card--grey" style="left:73px; top:451px;">
    <p class="wordmark wordmark--large">Trevantiq</p>
    <p class="web">www.trevantiq.example</p>
  </section>

  <p class="view-label" style="left:787px; top:410px;">Back - 3</p>
  <section class="card card--white" style="left:633px; top:450px;">
    <p class="wordmark wordmark--large">Trevantiq</p>
    <p class="web">www.trevantiq.example</p>
  </section>
</body>
</html>
```